Photoshop Templates for Instagram, x 2

A Square template to reuse that is on brand.

It will involve an image and text of between 3 and 10 words.
I would like 2 separate contrasting images to use interchangeably

In the files I have added some of the images that I have been using, as well as the home page of my website that is currently being developed.

The on brand would be very recognisable with the website.

Requirements
Must have
• Must be similar in feel to the home page.

Must be simple to to change image and and text in the template

I would like 2 designs. Both similar, but contrasting

The square images show the look that I have been using (created by myself, so I'm sure these can be massively improved upon)

```html
<!DOCTYPE html>
<html lang="en">
<head>
<meta charset="utf-8">
<title>Don't Let Yesterday Take Up Too Much Of Today</title>
<link rel="stylesheet" href="https://fonts.googleapis.com/css2?family=Montserrat:wght@700;800&display=swap">
<style>
  :root {
    --ink: #1b1a20;
    --brand-blue: #008ccf;
    --band-blue: rgba(34, 178, 226, 0.92);
    --sky-dark: #222326;
    --sky-mid: #55585b;
    --flood-light: #e6e9ea;
    --grass-light: #3d7d2c;
    --grass-dark: #1f4a18;
  }
  html, body {
    margin: 0;
    padding: 0;
    width: 1200px;
    height: 1200px;
    overflow: hidden;
    background: var(--sky-dark);
  }
  .post {
    position: relative;
    width: 1200px;
    height: 1200px;
    overflow: hidden;
    font-family: "Montserrat", sans-serif;
  }
  .post__backdrop {
    position: absolute;
    inset: 0;
    background:
      linear-gradient(to bottom,
        var(--sky-dark) 0px,
        #2b2c30 180px,
        var(--sky-mid) 300px,
        #cfd3d5 400px,
        var(--flood-light) 470px,
        #c9cdcf 560px,
        #6c7072 660px,
        #3e4143 725px,
        var(--grass-light) 740px,
        #2f6a23 900px,
        var(--grass-dark) 1200px);
  }
  .post__band {
    position: absolute;
    left: 0;
    top: 778px;
    width: 1200px;
    height: 186px;
    background: var(--band-blue);
  }
  .post__headline {
    position: absolute;
    inset: 0;
  }
  .headline__line { font-weight: 800; fill: var(--ink); }
  .headline__line--accent { fill: var(--brand-blue); }
  .headline__line--small { font-weight: 700; }
  .headline__rule { stroke: var(--ink); stroke-width: 4; stroke-linecap: round; }
</style>
</head>
<body>
  <main class="post">
    <div class="post__backdrop" role="img" aria-label="Photo of a floodlit football stadium at night with the green pitch and halfway line in the foreground"></div>
    <div class="post__band"></div>
    <svg class="post__headline" width="1200" height="1200" viewBox="0 0 1200 1200" aria-label="Don't let yesterday take up too much of today">
      <text class="headline__line" x="130" y="404" font-size="182" textLength="945" lengthAdjust="spacingAndGlyphs">DON’T LET</text>
      <text class="headline__line headline__line--accent" x="137" y="593" font-size="160" textLength="931" lengthAdjust="spacingAndGlyphs">YESTERDAY</text>
      <text class="headline__line headline__line--small" x="114" y="706" font-size="90" textLength="967" lengthAdjust="spacingAndGlyphs">TAKE UP TOO MUCH</text>
      <line class="headline__rule" x1="118" y1="739" x2="1080" y2="739"/>
      <text class="headline__line" x="122" y="932" font-size="190" textLength="962" lengthAdjust="spacingAndGlyphs">OF TODAY</text>
    </svg>
  </main>
</body>
</html>
```